Verpackungsdesign für Wellness- und Saunaprodukte
Zielgruppe
BaFinn ist ein junges Start-Up, das sich auf Wellness- und Saunaprodukte spezialisiert hat. Unsere Zielgruppe besteht zu beinahe gleichen Teilen aus männlichen und weiblichen Personen zwischen 30 und 60 Jahren. Unsere Produkte befinden sich eher im mittel- bis höherpreisigen Segment, daher streben wir ein hochwertiges Design für unsere Verpackungen an. Unsere Produktpalette reicht von Mentholkristallen, Saunaaufgüssen, bis hin zu Textilien für den Wellnessbereich und soll dementsprechend Menschen ansprechen, die sich einen gewissen Luxus im Alltag auch gönnen.
Aufgabenstellung
Inspiriert von der skandinavischen Sauna Kultur, möchten wir Momente der Erholung und
Entspannung in den Alltag unserer Kunden bringen. Die Geschichte des Saunierens ist eng mit der skandinavischen Kultur verbunden und skandinavische Stilelemente sind zeitgemäß und sprechen ein breites Publikum an. Das Design muss auf Dosen/Tiegel , Karton Verpackungen und Flaschen verschiedener Größen adaptierbar sein (siehe Bild im Anhang).
40g Tiegel(transparent) Höhe 40mm Durchmesser 60mm (ohne Deckel Silber gebürstet)
100g Tiegel(transparent) Höhe 53mm Durchmesser 71mm (ohne Deckel Silber gebürstet)
200g Tiegel(transparent) Höhe 65mm Durchmesser 90mm (ohne Deckel Silber gebürstet)
Karton Verpackung 124,5x49x49mm
Karton Verpackung 100x100x100mm
Flaschenetikett 134x67mm (Braunglas, schwarzer Deckel)
Es soll ein passendes Keyvisual erstellt werden.
Im Anhang sieht man die Verpackungen, Dosen, Flaschen sowie unsere ersten Design Entwürfe (an diese Anordnung der Elemente kann sich der Designer orientieren ). Das Logo bleibt wie gegeben. Das Produkt für die Tiegel soll Mentholkristalle sein.

```html
<!DOCTYPE html>
<html lang="de">
<head>
<meta charset="utf-8">
<title>BaFinn – Flaschenetiketten</title>
<link rel="stylesheet" href="https://fonts.googleapis.com/css2?family=Nunito:wght@400;800&family=Dancing+Script:wght@500&display=swap">
<style>
  :root {
    --canvas: #ffffff;
    --label-paper: #f4f2f1;
    --fichte-band: #bccdb8;
    --fichte-ink: #2e4a3a;
    --fichte-art: #d9e2d6;
    --menthol-band: #b8dad1;
    --menthol-ink: #2b7676;
    --menthol-art: #d6e9e4;
    --granat-band: #eba3a5;
    --granat-ink: #b05a64;
    --granat-art: #f3d3d4;
    --title: #ffffff;
    --brand: #6f6f6f;
  }
  html, body {
    margin: 0;
    width: 1200px;
    height: 848px;
    overflow: hidden;
    background: var(--canvas);
  }
  .label-set {
    position: relative;
    width: 1200px;
    height: 848px;
    display: flex;
    justify-content: center;
    align-items: center;
    gap: 90px;
  }
  .label {
    position: relative;
    width: 230px;
    height: 460px;
    background: var(--label-paper);
    box-shadow: 0 1px 4px rgba(0,0,0,0.12);
    overflow: hidden;
  }
  .label__band {
    position: absolute;
    left: 0;
    right: 0;
    top: 24%;
    height: 52%;
    background: var(--band);
  }
  .label__art {
    position: absolute;
    top: 2%;
    height: 31%;
    background: linear-gradient(180deg, var(--art) 0%, var(--band) 100%);
    opacity: 0.85;
  }
  .label--fichte .label__art { left: 18%; right: 0; }
  .label--menthol .label__art { left: 0; right: 30%; }
  .label--granat .label__art { left: 6%; right: 18%; }
  .label__title {
    position: absolute;
    left: 0;
    right: 0;
    top: 43%;
    margin: 0;
    text-align: center;
    font-family: "Nunito", sans-serif;
    font-weight: 800;
    font-size: 31px;
    line-height: 1.1;
    letter-spacing: 0.5px;
    color: var(--title);
  }
  .label__tagline {
    position: absolute;
    left: 0;
    right: 0;
    top: 66%;
    margin: 0;
    text-align: center;
    font-family: "Dancing Script", cursive;
    font-weight: 500;
    font-size: 18px;
    color: var(--ink);
  }
  .label__brand {
    position: absolute;
    left: 0;
    right: 0;
    bottom: 5%;
    display: flex;
    flex-direction: column;
    align-items: center;
    gap: 3px;
    font-family: "Nunito", sans-serif;
    font-weight: 400;
    font-size: 12px;
    color: var(--brand);
  }
  .label__brand-dot {
    width: 20px;
    height: 20px;
    border: 1.5px solid var(--brand);
    border-radius: 50%;
    box-sizing: border-box;
  }
  .label--fichte { --band: var(--fichte-band); --ink: var(--fichte-ink); --art: var(--fichte-art); }
  .label--menthol { --band: var(--menthol-band); --ink: var(--menthol-ink); --art: var(--menthol-art); }
  .label--granat { --band: var(--granat-band); --ink: var(--granat-ink); --art: var(--granat-art); }
</style>
</head>
<body>
  <main class="label-set">
    <article class="label label--fichte">
      <div class="label__band"></div>
      <div class="label__art" role="img" aria-label="Gezeichnete Fichtengruppe auf einer Wiese"></div>
      <h2 class="label__title">NORDISCHE<br>FICHTE</h2>
      <p class="label__tagline">Auszeit in der Flasche</p>
      <div class="label__brand"><span class="label__brand-dot"></span><span>BaFinn</span></div>
    </article>
    <article class="label label--menthol">
      <div class="label__band"></div>
      <div class="label__art" role="img" aria-label="Gezeichnete Minzblätter"></div>
      <h2 class="label__title">MENTHOL<br>KRISTALLE</h2>
      <p class="label__tagline">Auszeit in der Flasche</p>
      <div class="label__brand"><span class="label__brand-dot"></span><span>BaFinn</span></div>
    </article>
    <article class="label label--granat">
      <div class="label__band"></div>
      <div class="label__art" role="img" aria-label="Gezeichnete Granatäpfel am Zweig"></div>
      <h2 class="label__title">GRANAT<br>APFEL</h2>
      <p class="label__tagline">Auszeit in der Flasche</p>
      <div class="label__brand"><span class="label__brand-dot"></span><span>BaFinn</span></div>
    </article>
  </main>
</body>
</html>
```